Business Card Design Project

Business Card
We are rebranding with a new logo
Industry/Entity Type
Business
Contact Information for Business Card
Dennis Morvale +61 487215963 dennis@quorv.com.au P.O. Box 872 Fernlow QLD 4309
Requirements
Must have
- Logo

```html
<!DOCTYPE html>
<html lang="en">
<head>
<meta charset="utf-8">
<title>Quorv International — Business Card</title>
<link rel="stylesheet" href="https://fonts.googleapis.com/css2?family=Roboto:wght@400;500;700&display=swap">
<style>
  :root {
    --backdrop: #2a2a2b;
    --blue-deep: #075272;
    --blue-soft: #1688bb;
    --paper: #f1f1f1;
    --ink-light: #ffffff;
    --brand-blue: #0d77a8;
  }
  * { margin: 0; padding: 0; box-sizing: border-box; }
  html, body {
    width: 1200px;
    height: 960px;
    overflow: hidden;
    background: var(--backdrop);
    font-family: "Roboto", Arial, sans-serif;
  }
  .business-card {
    position: absolute;
    left: 223px;
    top: 265px;
    width: 754px;
    height: 430px;
    border-radius: 18px;
    overflow: hidden;
    background: var(--paper);
  }
  .artwork-panel {
    position: absolute;
    inset: 0;
    background: linear-gradient(135deg, var(--blue-deep) 0%, var(--blue-soft) 55%, var(--blue-deep) 100%);
    clip-path: polygon(0 0, 744px 0, 222px 430px, 0 430px);
  }
  .contact-block {
    position: absolute;
    left: 50px;
    top: 66px;
    color: var(--ink-light);
  }
  .holder-name {
    font-weight: 700;
    font-size: 23px;
    line-height: 1;
    margin-bottom: 20px;
  }
  .postal-address {
    font-size: 17px;
    line-height: 23px;
    margin-bottom: 9px;
  }
  .contact-list { list-style: none; }
  .contact-item {
    display: flex;
    align-items: center;
    font-size: 17px;
    line-height: 24px;
  }
  .contact-icon {
    width: 16px;
    height: 16px;
    margin-right: 12px;
    fill: var(--ink-light);
    flex-shrink: 0;
  }
  .brand-name {
    position: absolute;
    right: 62px;
    top: 282px;
    text-align: right;
    color: var(--brand-blue);
    font-weight: 500;
    line-height: 1.1;
  }
  .brand-name .brand-word { display: block; font-size: 52px; letter-spacing: 1px; }
  .brand-name .brand-tag { display: block; font-size: 21px; letter-spacing: 3px; margin-top: 4px; }
</style>
</head>
<body>
  <section class="business-card">
    <div class="artwork-panel" role="img" aria-label="Blue decorative panel with abstract swoosh artwork"></div>

    <div class="contact-block">
      <h1 class="holder-name">DENNIS MORVALE</h1>
      <p class="postal-address">P.O. Box 872<br>Fernlow QLD 4309</p>
      <ul class="contact-list">
        <li class="contact-item">
          <svg class="contact-icon" viewBox="0 0 16 16"><path d="M3.5 1 L6 1 L7 4.5 L5.3 6 C6.2 8 8 9.8 10 10.7 L11.5 9 L15 10 L15 12.5 C15 13.9 13.9 15 12.5 15 C6.7 15 1 9.3 1 3.5 C1 2.1 2.1 1 3.5 1 Z"/></svg>
          +61 487215963
        </li>
        <li class="contact-item">
          <svg class="contact-icon" viewBox="0 0 16 16"><path d="M1 3 H15 V4 L8 9 L1 4 Z M1 5.3 L8 10.3 L15 5.3 V13 H1 Z"/></svg>
          dennis@quorv.com.au
        </li>
        <li class="contact-item">
          <svg class="contact-icon" viewBox="0 0 16 16"><path d="M8 1 A7 7 0 1 0 8 15 A7 7 0 1 0 8 1 Z M5 4 L8 3.5 L9 5.5 L7 7 L5 6.5 Z M9.5 8.5 L12.5 9 L11 12.5 L9 11.5 Z"/></svg>
          www.quorv.com.au
        </li>
      </ul>
    </div>

    <div class="brand-name">
      <span class="brand-word">Quorv</span>
      <span class="brand-tag">INTERNATIONAL</span>
    </div>
  </section>
</body>
</html>
```